need corporate, modern business card created for Consulting Company

I need a slick business card using elements from my website, as well as, integrating my pixelforge-created logo (see files).

The business card needs to be:
1. Corporate and modern
2. Clean and professional

I've included a PSD with the logo/icon that you can use to create it. Feel free to try a metallic finish on the logo, make it bigger/small, underlay it. Whatever you need to do to make my card stand out.

Try a black background, or white background or gray.

The idea is for my card to be memorable as well as professional and corporate.

Target Market(s)

Corporate business in the US and Canada.

Industry/Entity Type

Business

Contact Information for Business Card

Commerce Advancing Methods
Martin Coles, Senior Partner
office: 1 877 555 0143
mobile: 1 519 555 0172
website: http://www.brightvale.example

Requirements
Must have
• Card-related information
• corporate, yet modern
• clean and professional
• incorporate the icon only
• must have an editable form when complete!
Nice to have
• metallic icon might be cool
• try it with white or black

```html
<!DOCTYPE html>
<html lang="en">
<head>
<meta charset="utf-8">
<title>Brightvale Business Card</title>
<link href="https://fonts.googleapis.com/css2?family=Open+Sans:ital,wght@0,300;0,400;0,600;0,700;1,700&display=swap" rel="stylesheet">
<style>
  :root {
    --backdrop: #e4e5e7;
    --card-black: #1d1e20;
    --brand-blue: #2f6bc2;
    --deep-navy: #1b2c5c;
    --band-grey: #8e939b;
    --band-white: #f4f5f7;
    --text-white: #ffffff;
    --text-muted: #c9ccd2;
  }
  * { margin: 0; padding: 0; box-sizing: border-box; }
  html, body { width: 1200px; height: 772px; overflow: hidden; }
  body {
    background: var(--backdrop);
    font-family: "Open Sans", Arial, sans-serif;
    position: relative;
  }
  .card {
    position: absolute;
    top: 231px;
    width: 540px;
    height: 309px;
    background: var(--card-black);
    overflow: hidden;
    box-shadow: 0 6px 18px rgba(0,0,0,0.18);
  }
  .card--front { left: 40px; }
  .card--back { left: 620px; }

  .wordmark {
    position: absolute;
    display: flex;
    align-items: center;
    gap: 12px;
  }
  .wordmark__square {
    background: var(--brand-blue);
  }
  .wordmark__name {
    color: var(--text-white);
    font-weight: 600;
    letter-spacing: 0.5px;
    line-height: 1;
  }
  .card--front .wordmark {
    left: 50%;
    top: 50%;
    transform: translate(-50%, -50%);
  }
  .card--front .wordmark__square { width: 34px; height: 34px; }
  .card--front .wordmark__name { font-size: 52px; }

  .card--back .wordmark { right: 40px; top: 34px; gap: 8px; }
  .card--back .wordmark__square { width: 18px; height: 18px; }
  .card--back .wordmark__name { font-size: 28px; }

  .wave {
    position: absolute;
    inset: 0;
    width: 100%;
    height: 100%;
  }
  .wave__grey { fill: var(--band-grey); }
  .wave__white { fill: var(--band-white); }
  .wave__navy { fill: var(--deep-navy); }
  .wave__blue { fill: var(--brand-blue); }

  .person {
    position: absolute;
    left: 34px;
    top: 34px;
    color: var(--text-white);
  }
  .person__name {
    font-size: 20px;
    font-weight: 700;
    font-style: italic;
  }
  .person__role {
    font-size: 16px;
    font-weight: 300;
    color: var(--text-muted);
    margin-top: 2px;
  }

  .contact {
    position: absolute;
    right: 30px;
    bottom: 24px;
    list-style: none;
    text-align: right;
    color: var(--text-white);
    font-size: 12px;
    line-height: 18px;
  }
  .contact__item {
    display: flex;
    justify-content: flex-end;
    align-items: center;
    gap: 6px;
  }
  .contact__icon {
    width: 10px;
    height: 10px;
    fill: var(--text-white);
  }
</style>
</head>
<body>

  <section class="card card--front" aria-label="Card front">
    <div class="wordmark">
      <span class="wordmark__square"></span>
      <span class="wordmark__name">brightvale</span>
    </div>
  </section>

  <section class="card card--back" aria-label="Card back">
    <svg class="wave" viewBox="0 0 540 309" aria-hidden="true">
      <path class="wave__grey" d="M0,104 C150,84 230,194 360,174 C430,164 500,124 540,114 L540,309 L0,309 Z"/>
      <path class="wave__white" d="M0,116 C150,96 230,206 360,186 C430,176 500,136 540,126 L540,309 L0,309 Z"/>
      <path class="wave__navy" d="M0,122 C150,102 230,212 360,192 C430,182 500,142 540,132 L540,309 L0,309 Z"/>
      <path class="wave__blue" d="M0,134 C150,114 230,224 360,204 C430,194 500,154 540,144 L540,309 L0,309 Z"/>
    </svg>

    <div class="person">
      <p class="person__name">Dara Whitfield-Lane</p>
      <p class="person__role">Consultant</p>
    </div>

    <div class="wordmark">
      <span class="wordmark__square"></span>
      <span class="wordmark__name">brightvale</span>
    </div>

    <ul class="contact">
      <li class="contact__item">214 9th floor, Quay
        <svg class="contact__icon" viewBox="0 0 10 10"><path d="M5 0a3.5 3.5 0 0 0-3.5 3.5C1.5 6 5 10 5 10s3.5-4 3.5-6.5A3.5 3.5 0 0 0 5 0zm0 5a1.5 1.5 0 1 1 0-3 1.5 1.5 0 0 1 0 3z"/></svg>
      </li>
      <li class="contact__item">Harbour Street NTW</li>
      <li class="contact__item">019 555 0146
        <svg class="contact__icon" viewBox="0 0 10 10"><path d="M2 0l2 2.5-1 1.2a6 6 0 0 0 3.3 3.3l1.2-1L10 8l-1.5 2C4 10 0 6 0 1.5z"/></svg>
      </li>
      <li class="contact__item">dara@brightvale.example
        <svg class="contact__icon" viewBox="0 0 10 10"><path d="M0 2h10v6H0zM0.6 2.4L5 5.6 9.4 2.4" stroke="#1d1e20" stroke-width="0.8"/></svg>
      </li>
      <li class="contact__item">www.brightvale.example
        <svg class="contact__icon" viewBox="0 0 10 10"><circle cx="5" cy="5" r="4.3" fill="none" stroke="#fff" stroke-width="1"/><path d="M0.7 5h8.6M5 0.7v8.6" stroke="#fff" stroke-width="0.8"/></svg>
      </li>
    </ul>
  </section>

</body>
</html>
```